Business Card Design

We need a business card designed for our new company. Prefer a black card with white logo & writing.

Contact Information for Business Card

Ted Galloway, address: 7-4812 Fernhollow Road, Abbotsford, BC, V3K 8R2, Office Phone: 604-712-3390, Cell: 604-947-2164, Email: ted@resinworkshub.ca

Colors

Designer to choose only greyscale colors for use in the design.

```html
<!DOCTYPE html>
<html lang="en">
<head>
<meta charset="utf-8">
<title>Resinworks Hub – Business Card</title>
<link rel="stylesheet" href="https://fonts.googleapis.com/css2?family=Poppins:wght@300;400;700&display=swap">
<style>
  :root {
    --backdrop: #e6e6e6;
    --card: #1f1f21;
    --card-pattern-light: #2c2c2f;
    --card-pattern-dark: #18181a;
    --ink: #ffffff;
    --ink-soft: #d9d9d9;
  }
  * { box-sizing: border-box; margin: 0; padding: 0; }
  html, body {
    width: 1200px; height: 780px; overflow: hidden;
    background: var(--backdrop);
    font-family: "Poppins", sans-serif;
  }
  .sheet {
    width: 1200px; height: 780px;
    display: flex; align-items: center; justify-content: center; gap: 30px;
  }
  .card {
    position: relative;
    width: 560px; height: 320px;
    background: var(--card);
    color: var(--ink);
    box-shadow: 0 6px 18px rgba(0,0,0,.25);
    overflow: hidden;
  }

  /* Front */
  .name-bar {
    position: absolute; left: 0; top: 44px;
    width: 14px; height: 60px; background: var(--ink);
  }
  .identity { position: absolute; left: 30px; top: 40px; }
  .identity .name { font-size: 30px; line-height: 1.1; font-weight: 300; }
  .identity .name strong { font-weight: 700; }
  .identity .role { font-size: 15px; font-weight: 300; margin-top: 2px; }

  .address {
    position: absolute; left: 96px; top: 150px;
    font-size: 14px; font-weight: 300; line-height: 1.4;
  }
  .contact {
    position: absolute; left: 96px; top: 208px;
    list-style: none; font-size: 14px; font-weight: 300;
  }
  .contact li { display: flex; align-items: center; height: 21px; }
  .contact svg { width: 14px; height: 14px; margin-right: 10px; flex: none; }

  .brand {
    position: absolute; right: 34px; top: 96px;
    width: 200px; text-align: center;
    font-weight: 700; color: var(--ink);
    line-height: 1;
  }
  .brand .mark {
    display: block; width: 26px; height: 26px; margin: 0 auto 10px;
    border-radius: 50%; background: var(--ink);
  }
  .brand .word { display: block; font-size: 32px; letter-spacing: .5px; }
  .brand .word + .word { font-size: 32px; margin-top: 4px; }

  /* Back */
  .pattern {
    position: absolute; inset: 0;
    background: linear-gradient(135deg, var(--card-pattern-light), var(--card-pattern-dark));
  }
  .back-brand {
    position: absolute; left: 345px; top: 150px;
    font-size: 13px; font-weight: 700; color: var(--ink);
    display: flex; align-items: center; gap: 6px;
  }
  .back-brand .mark {
    width: 9px; height: 9px; border-radius: 50%; background: var(--ink);
  }
</style>
</head>
<body>
<main class="sheet">
  <section class="card card-front" aria-label="Business card front">
    <div class="name-bar"></div>
    <div class="identity">
      <p class="name"><strong>Ted</strong> Galloway</p>
      <p class="role">Founder &amp; CEO</p>
    </div>
    <address class="address" style="font-style:normal">
      7-4812 Fernhollow Road,<br>
      Abbotsford, BC, V3K 8R2.
    </address>
    <ul class="contact">
      <li>
        <svg viewBox="0 0 14 14" aria-hidden="true"><circle cx="7" cy="7" r="7" fill="#fff"/><path d="M4.3 3.5l1.6 1.7-.8 1a5 5 0 0 0 2.7 2.7l1-.8 1.7 1.6-.9 1a6.5 6.5 0 0 1-6.3-6.3z" fill="#1f1f21"/></svg>
        604-712-3390
      </li>
      <li>
        <svg viewBox="0 0 14 14" aria-hidden="true"><rect width="14" height="14" rx="2" fill="#fff"/><rect x="4.5" y="2.5" width="5" height="9" rx="1" fill="#1f1f21"/><circle cx="7" cy="10" r=".6" fill="#fff"/></svg>
        604-947-2164
      </li>
      <li>
        <svg viewBox="0 0 14 14" aria-hidden="true"><circle cx="7" cy="7" r="7" fill="#fff"/><g fill="none" stroke="#1f1f21" stroke-width=".9"><circle cx="7" cy="7" r="4.6"/><ellipse cx="7" cy="7" rx="2" ry="4.6"/><path d="M2.4 7h9.2"/></g></svg>
        www.resinworkshub.ca
      </li>
      <li>
        <svg viewBox="0 0 14 14" aria-hidden="true"><rect y="2" width="14" height="10" rx="1.5" fill="#fff"/><path d="M1.5 3.5L7 8l5.5-4.5" fill="none" stroke="#1f1f21" stroke-width="1"/></svg>
        ted@resinworkshub.ca
      </li>
    </ul>
    <div class="brand">
      <span class="mark"></span>
      <span class="word">RESINWORKS</span>
      <span class="word">HUB</span>
    </div>
  </section>

  <section class="card card-back" aria-label="Business card back">
    <div class="pattern" role="img" aria-label="Tonal repeating brand emblem pattern across the card"></div>
    <div class="back-brand"><span class="mark"></span>RESINWORKS HUB</div>
  </section>
</main>
</body>
</html>
```